MES Modul-Struktur grafisch veranschaulichen
Zielgruppe
Wir sind Software-Hersteller. Thema 'MES'. Unsere Kunden sind Produktionsunternehmen.
Mit einem MES (Manufacturing Execution System) werden Produktionsprozesse überwacht, geplant, gesteuert und optimiert. Allgemein geht es darum, die Produktivität zu steigern und Kosten zu minimieren.
Eine MES-Software ist modular strukturiert, so dass der Kunde sich nach Bedarf die einzelnen Funktionsmodule zusammenstellen kann. Unser MES KORVIN 7 MAX besteht z.B. aus folgenden Einzelmodulen:
- BASIS (Basismodul)
- MDE (Maschinendatenerfassung)
- BDE (Betriebsdatenerfassung)
- INST (Instandhaltung)
- ALARM (Alarmierung)
- DOK (Dokumentenmanagement)
- TNT (Traceability)
- PLAN (Feinplanung/Leitstand)
- LOG (Logistik)
- VIS (Visualisierung)
- PEP (Personaleinsatzplanung)
- MPZE (Personalzeiterfassung)
- DNC (Rezepturen/DNC)
- EM (Energiemonitoring)
Aufgabenstellung
Die modulare Struktur und der große Umfang an Modulen ist ein wichtiger Vorteil für unsere Kunden, da Sie nicht so schnell an Grenzen stoßen und sich dann unter Umständen eine weitere Insellösung (extra Software mit extra Datenbank ...) anschaffen müssen.
Wichtig ist, dass die einzelnen Module funktionell ineinandergreifen und alle auf die gleiche Datenbank zugreifen.
Es reicht wenn in der Grafik die Module nur mit er Abkürzung, also z.B. MDE bezeichnet werden. Für den ersten Entwurf können auch Platzhalter genutzt werden.
Der Betrachter sollte aus der Grafik auf den ersten Blick erkennen:
- umfängliches MES
- modular strukturiert
- Funktionsmodule step-by-step erweiterbar
Für die Umsetzung naheliegend wären Puzzle-Steine, Blokkis, ... muss aber nicht.

```html
<!DOCTYPE html>
<html lang="de">
<head>
<meta charset="utf-8">
<title>MES Modul-Struktur</title>
<link rel="stylesheet" href="https://fonts.googleapis.com/css2?family=Open+Sans:wght@400;700&family=Roboto+Condensed:wght@700&display=swap">
<style>
  :root {
    --bg: #ffffff;
    --ink: #111111;
    --process: #d9d9d9;
    --hub: #000000;
    --label: #ffffff;
    --basis: #b07d48;
    --mde: #e55b13;
    --bde-green: #95be0e;
    --bde: #2da8da;
    --inst: #a0105a;
    --alarm: #e3001b;
    --mde-yellow: #ddd900;
    --dok: #0e2d82;
    --tnt: #0b8a33;
    --plan: #ae7c48;
    --log: #ee8e69;
    --vis: #72b8e2;
    --pep: #c2705a;
    --mpze: #e3c29c;
    --dnc: #f0cc84;
    --em: #f6eeb8;
    --extra: #edb8d4;
  }
  html, body {
    margin: 0;
    padding: 0;
    width: 1200px;
    height: 848px;
    overflow: hidden;
    background: var(--bg);
  }
  .canvas { display: block; width: 1200px; height: 848px; }
  .stage-title { font-family: "Open Sans", sans-serif; font-size: 21px; fill: var(--ink); }
  .process-area { fill: var(--process); }
  .process-label { font-family: "Open Sans", sans-serif; font-size: 22px; fill: var(--label); }
  .hub { fill: var(--hub); }
  .hub-label { font-family: "Roboto Condensed", sans-serif; font-weight: 700; font-size: 19px; fill: var(--label); letter-spacing: -0.5px; }
  .module use { stroke: var(--bg); stroke-width: 3.5; stroke-linejoin: miter; }
  .module-label { font-family: "Open Sans", sans-serif; font-weight: 700; font-size: 19px; fill: var(--label); }
  .module-label--small { font-size: 15px; }
  .m-basis { fill: var(--basis); }
  .m-mde { fill: var(--mde); }
  .m-bde-green { fill: var(--bde-green); }
  .m-bde { fill: var(--bde); }
  .m-inst { fill: var(--inst); }
  .m-alarm { fill: var(--alarm); }
  .m-mde-yellow { fill: var(--mde-yellow); }
  .m-dok { fill: var(--dok); }
  .m-tnt { fill: var(--tnt); }
  .m-plan { fill: var(--plan); }
  .m-log { fill: var(--log); }
  .m-vis { fill: var(--vis); }
  .m-pep { fill: var(--pep); }
  .m-mpze { fill: var(--mpze); }
  .m-dnc { fill: var(--dnc); }
  .m-em { fill: var(--em); }
  .m-extra { fill: var(--extra); }
</style>
</head>
<body>
<svg class="canvas" viewBox="0 0 1750 1240" preserveAspectRatio="none" xmlns="http://www.w3.org/2000/svg" xmlns:xlink="http://www.w3.org/1999/xlink">
  <defs>
    <path id="module-band" d="M -33.08 -296.15 A 298 298 0 0 1 33.08 -296.15 L 21.65 -193.79 A 195 195 0 0 0 -21.65 -193.79 Z"/>
    <path id="module-link-a" d="M -21.65 -193.79 A 195 195 0 0 1 0 -195 L 0 -36 A 36 36 0 0 0 -4 -35.78 Z"/>
    <path id="module-link-b" d="M 0 -195 A 195 195 0 0 1 21.65 -193.79 L 4 -35.78 A 36 36 0 0 0 0 -36 Z"/>
    <g id="module-shape">
      <use xlink:href="#module-band"/>
      <use xlink:href="#module-link-a"/>
      <use xlink:href="#module-link-b"/>
    </g>
  </defs>

  <!-- Stufe 1: Basis -->
  <g class="stage stage--basis">
    <text class="stage-title" x="362" y="63" text-anchor="middle">Basis Modul</text>
    <circle class="process-area" cx="367" cy="395" r="257"/>
    <g transform="translate(366 390)">
      <g class="module m-basis" transform="rotate(0)"><use xlink:href="#module-shape"/><text class="module-label" x="0" y="-273" text-anchor="middle">BASIS</text></g>
    </g>
    <circle class="hub" cx="366" cy="390" r="35"/>
    <text class="hub-label" x="366" y="397" text-anchor="middle">KUNDE</text>
    <text class="process-label" x="366" y="465" text-anchor="middle">Produktionsprozesse</text>
  </g>

  <!-- Stufe 2: Basis + 2 -->
  <g class="stage stage--plus-two">
    <text class="stage-title" x="945" y="63" text-anchor="middle">Basis + 2 Modul</text>
    <circle class="process-area" cx="914" cy="395" r="257"/>
    <g transform="translate(913 390)">
      <g class="module m-basis" transform="rotate(0)"><use xlink:href="#module-shape"/><text class="module-label" x="0" y="-273" text-anchor="middle">BASIS</text></g>
      <g class="module m-mde" transform="rotate(12.75)"><use xlink:href="#module-shape"/><text class="module-label" x="0" y="-273" text-anchor="middle">MDE</text></g>
      <g class="module m-bde-green" transform="rotate(25.5)"><use xlink:href="#module-shape"/><text class="module-label" x="0" y="-273" text-anchor="middle">BDE</text></g>
    </g>
    <circle class="hub" cx="913" cy="390" r="35"/>
    <text class="hub-label" x="913" y="397" text-anchor="middle">KUNDE</text>
    <text class="process-label" x="913" y="461" text-anchor="middle">Produktionsprozesse</text>
  </g>

  <!-- Stufe 3: Basis + 3 -->
  <g class="stage stage--plus-three">
    <text class="stage-title" x="1497" y="63" text-anchor="middle">Basis + 3 Modul</text>
    <circle class="process-area" cx="1464" cy="398" r="257"/>
    <g transform="translate(1464 392)">
      <g class="module m-basis" transform="rotate(0)"><use xlink:href="#module-shape"/><text class="module-label" x="0" y="-273" text-anchor="middle">BASIS</text></g>
      <g class="module m-mde" transform="rotate(12.75)"><use xlink:href="#module-shape"/><text class="module-label" x="0" y="-273" text-anchor="middle">MDE</text></g>
      <g class="module m-bde" transform="rotate(25.5)"><use xlink:href="#module-shape"/><text class="module-label" x="0" y="-273" text-anchor="middle">BDE</text></g>
      <g class="module m-inst" transform="rotate(38.25)"><use xlink:href="#module-shape"/><text class="module-label" x="0" y="-273" text-anchor="middle">INST</text></g>
    </g>
    <circle class="hub" cx="1464" cy="392" r="35"/>
    <text class="hub-label" x="1464" y="399" text-anchor="middle">KUNDE</text>
    <text class="process-label" x="1464" y="465" text-anchor="middle">Produktionsprozesse</text>
  </g>

  <!-- Stufe 4: Vollausbau -->
  <g class="stage stage--full">
    <text class="stage-title" x="300" y="752">Etc ...</text>
    <circle class="process-area" cx="607" cy="920" r="257"/>
    <g transform="translate(607 916)">
      <g class="module m-basis" transform="rotate(0)"><use xlink:href="#module-shape"/><text class="module-label" x="0" y="-273" text-anchor="middle">BASIS</text></g>
      <g class="module m-mde" transform="rotate(12.75)"><use xlink:href="#module-shape"/><text class="module-label" x="0" y="-273" text-anchor="middle">MDE</text></g>
      <g class="module m-bde" transform="rotate(25.5)"><use xlink:href="#module-shape"/><text class="module-label" x="0" y="-273" text-anchor="middle">BDE</text></g>
      <g class="module m-inst" transform="rotate(38.25)"><use xlink:href="#module-shape"/><text class="module-label" x="0" y="-273" text-anchor="middle">INST</text></g>
      <g class="module m-alarm" transform="rotate(51)"><use xlink:href="#module-shape"/><text class="module-label module-label--small" x="0" y="-275" text-anchor="middle">ALARM</text></g>
      <g class="module m-mde-yellow" transform="rotate(63.75)"><use xlink:href="#module-shape"/><text class="module-label" x="0" y="-273" text-anchor="middle">MDE</text></g>
      <g class="module m-dok" transform="rotate(76.5)"><use xlink:href="#module-shape"/><text class="module-label" x="0" y="-273" text-anchor="middle">DOK</text></g>
      <g class="module m-tnt" transform="rotate(89.25)"><use xlink:href="#module-shape"/><text class="module-label" x="0" y="-273" text-anchor="middle">TNT</text></g>
      <g class="module m-plan" transform="rotate(102)"><use xlink:href="#module-shape"/><text class="module-label" x="0" y="-273" text-anchor="middle">PLAN</text></g>
      <g class="module m-log" transform="rotate(114.75)"><use xlink:href="#module-shape"/></g>
      <g class="module m-vis" transform="rotate(127.5)"><use xlink:href="#module-shape"/></g>
      <g class="module m-pep" transform="rotate(140.25)"><use xlink:href="#module-shape"/></g>
      <g class="module m-mpze" transform="rotate(153)"><use xlink:href="#module-shape"/></g>
      <g class="module m-dnc" transform="rotate(165.75)"><use xlink:href="#module-shape"/></g>
      <g class="module m-em" transform="rotate(178.5)"><use xlink:href="#module-shape"/></g>
      <g class="module m-extra" transform="rotate(191.25)"><use xlink:href="#module-shape"/></g>
    </g>
    <circle class="hub" cx="607" cy="916" r="35"/>
    <text class="hub-label" x="607" y="923" text-anchor="middle">KUNDE</text>
    <text class="process-label" x="565" y="923" text-anchor="end">Produktionsprozesse</text>
  </g>
</svg>
</body>
</html>
```